I need a label created within the following dimensions below:

Label/Screen Printable Area:

Width 6.742”

Height 5.731”

The bottle dimensions are 7.175 (H) x 2.146 (D)
Updates

This is for 2 seperate labels.  One label for my hair Shampoo and another label for my hair Conditioner.

Requirements
Must have
• Front of Shampoo bottle:

Verdant Quiet Harbors logo

Product name (shampoo – Nourishing & Hydrating)

Bottle volume: 12 fl. Oz. (355ml)

Side of bottle:

"Verdant Restoring with clear oil Tonics"

Back of bottle:

Verdant Quiet Harbors Shampoo is a blend of heavenly, ingredients from Mother Earth that nourish, protect and beautify your hair and extend the life of color. Our Products are Sulfate-Free, Paraben-Free, Contain No Artificial Colors and are Not Tested on Animals.

Distributed By and/or Get more information: (Distributed By: Quiet Harbors, Brookmere, IL 60999/ Get more information and connect with Quiet Harbors at www.verdantquietharborsco.example)

Ingredients: (I’ve included the ingredients listings below for quick copying to your art file)

DESCRIPTION: Quiet Harbors Shampoo

How to/ Directions for use: (Apply to wet hair. Massage into a rich lather. Rinse. Repeat if necessary.)

INGREDIENTS: Purified Water, Sodium Methyl 2-Sulfolaurate & Disodium 2-Sulfolaurate & Cocamidopropyl Betaine, Cetrimonium Chloride, Distearyl Phthalic Acid Amide, Simmondsia Chinensis (Organic Jojoba Seed) Oil, Butyrospermum Parkii (Organic Shea Butter) Fruit, Aloe Barbadensis Leaf Juice (Organic Aloe Vera Gel), Hydrolyzed Quinoa (Protein), Dimethicone, Fragrance (Apple, Pear, White Grape), Gluconolactone & Sodium Benzoate (Natural Preservative), Panthenol (Vitamin B-5), Citric Acid, Tocopherol (Vitamin E).

Front of conditioner bottle:

Product name: (Conditioner Shampoo - luxurious volume conditioner)

Side of bottle:

Back of bottle:

DESCRIPTION: Quiet Harbors Restructurant Conditioner

How to/ Directions for use: (Apply to wet hair. Massage into hair and sit for 5 minutes. For a deep conditoner treatment apply to hair and sit under the hair dryer for 20-30 minutes, Repeat if necessary; then rinse and style as usual).

INGREDIENTS: Purified Water, Behentrimonium Methosulfate (Modified Rapseed Oil), Cetearyl Alcohol, Cetyl Alcohol, Cetrimonium Chloride, Cyclopentasiloxane and Dimethicone, Caprylic/Capric Triglyceride, Extracts of Foeniculum Vulgare (Fennel Seed) and Helianthus Annuus (Sunflower Seed), Simmondsia Chinensis (Jojoba Seed) Oil, Olea Europaea (Olive Fruit) Oil, Fragrance, Mentha Piperita (Peppermint) Oil, Mentha (Menthol), Aloe Barbadensis Leaf Juice (Organic Aloe Vera Gel), Hydrolyzed Hair Keratin, Butyrospermum Parkii (Organic Shea Butter) Fruit, Sodium Benzoate (Natural Preservative) and Potassium Sorbate, Rosmarinus Officinalis (Rosemary) Oil, Lavandula Officinalis (Lavender) Oil, Panthenol (Vitamin B-5), Tocopherol (Vitamin E), Guar Hydroxypropyltrimonium Chloride, Citric Acid.

Width 6.742”

Height 5.731”

Should not have
• No other colors then what my logo colors currently are.

```html
<!DOCTYPE html>
<html lang="en">
<head>
<meta charset="utf-8">
<title>Verdant Quiet Harbors Shampoo Label</title>
<link href="https://fonts.googleapis.com/css2?family=Arimo:wght@400;700&display=swap" rel="stylesheet">
<style>
  :root{
    --gold:#a87b2f;
    --gold-text:#b08937;
    --green:#0c4a2c;
    --leaf-light:#b9dc5a;
    --leaf-dark:#5e9a24;
    --cream:#e9e0cf;
    --white:#ffffff;
  }
  html,body{margin:0;padding:0;overflow:hidden;background:var(--white);}
  .label{
    position:relative;width:1200px;height:1020px;overflow:hidden;
    background:var(--cream);
    font-family:"Arimo",Arial,sans-serif;
  }
  .backdrop{position:absolute;inset:0;}
  .brand{
    position:absolute;left:40px;top:150px;width:460px;text-align:center;
  }
  .brand-dot{
    width:26px;height:26px;border-radius:50%;background:var(--green);
    margin:0 auto 22px;
  }
  .brand-name{
    margin:0;color:var(--green);font-weight:700;font-size:40px;line-height:1.15;
  }
  .leaves{
    position:absolute;left:113px;top:448px;width:278px;height:170px;
  }
  .product-band{
    position:absolute;left:40px;top:627px;width:455px;height:123px;
    background:var(--gold);color:var(--white);text-align:center;
    display:flex;flex-direction:column;justify-content:center;
    font-weight:700;font-size:33px;line-height:1.25;
    text-shadow:2px 2px 2px rgba(0,0,0,.75);
  }
  .product-band p{margin:0;}
  .volume{
    position:absolute;left:255px;top:950px;margin:0;
    color:var(--gold);font-weight:700;font-size:27px;
  }
  .side-line{
    position:absolute;left:597px;top:494px;margin:0;white-space:nowrap;
    transform:translate(-50%,-50%) rotate(-90deg);
    color:var(--gold-text);font-weight:700;font-size:24px;
    text-shadow:0 0 2px var(--white),1px 1px 1px rgba(0,0,0,.35);
  }
  .back-copy{
    position:absolute;left:694px;width:462px;margin:0;
    color:var(--gold-text);font-weight:700;font-size:20.5px;line-height:25px;
    text-align:justify;
    text-shadow:0 0 2px var(--white),1px 1px 1px rgba(0,0,0,.35);
  }
  .description{top:86px;}
  .directions{top:332px;}
  .ingredients{top:491px;}
  .distributor{
    position:absolute;left:694px;top:903px;width:462px;height:88px;
    background:var(--gold);color:var(--white);box-sizing:border-box;
    padding:8px 12px;margin:0;font-weight:700;font-size:10px;line-height:22px;
  }
</style>
</head>
<body>
<div class="label">
  <svg class="backdrop" width="1200" height="1020" viewBox="0 0 1200 1020" aria-hidden="true">
    <path fill="#ffffff" d="M70,0 H470 C520,140 420,300 400,430 C380,560 470,760 520,1020 H0 V420 C90,380 130,260 70,0 Z"/>
    <path fill="#ffffff" d="M0,440 C120,420 200,520 160,700 C130,840 200,960 260,1020 H0 Z"/>
    <path fill="#ffffff" d="M640,0 H1080 C990,70 1010,220 1200,270 V1020 H700 C770,820 650,620 700,420 C740,260 680,110 640,0 Z"/>
  </svg>

  <div class="brand">
    <div class="brand-dot"></div>
    <p class="brand-name">Verdant Quiet Harbors</p>
  </div>

  <svg class="leaves" viewBox="0 0 278 170" role="img" aria-label="Illustration of three fresh green leaves">
    <defs>
      <radialGradient id="leafTone" cx="50%" cy="40%" r="60%">
        <stop offset="0%" stop-color="var(--leaf-light)"/>
        <stop offset="100%" stop-color="var(--leaf-dark)"/>
      </radialGradient>
    </defs>
    <ellipse cx="139" cy="85" rx="135" ry="80" fill="url(#leafTone)"/>
  </svg>

  <div class="product-band">
    <p>Shampoo</p>
    <p>Nourishing &amp; Hydrating</p>
  </div>

  <p class="volume">12 fl. Oz. (355ml)</p>

  <p class="side-line">Verdant Restoring with clear oil Tonics</p>

  <p class="back-copy description">Verdant Quiet Harbors Shampoo is a blend of heavenly, ingredients from Mother Earth that nourish, protect and beautify your hair and extend the life of color. Our Products are Sulfate-Free, Paraben-Free, Contain No Artificial Colors and are Not Tested on Animals.</p>

  <p class="back-copy directions">How to/ Directions for use: (Apply to wet hair. Massage into a rich lather. Rinse. Repeat if necessary.)</p>

  <p class="back-copy ingredients">INGREDIENTS: Purified Water, Sodium Methyl 2-Sulfolaurate &amp; Disodium 2-Sulfolaurate &amp; Cocamidopropyl Betaine, Cetrimonium Chloride, Distearyl Phthalic Acid Amide, Simmondsia Chinensis (Organic Jojoba Seed) Oil, Butyrospermum Parkii (Organic Shea Butter) Fruit, Aloe Barbadensis Leaf Juice (Organic Aloe Vera Gel), Hydrolyzed Quinoa (Protein), Dimethicone, Fragrance (Apple, Pear, White Grape), Gluconolactone &amp; Sodium Benzoate (Natural Preservative), Panthenol (Vitamin B-5), Citric Acid, Tocopherol (Vitamin E).</p>

  <p class="distributor">Distributed By and/or Get more information: (Distributed By: Quiet Harbors, Brookmere, IL 60999/ Get more information and connect with Quiet Harbors at www.verdantquietharborsco.example)</p>
</div>
</body>
</html>
```